Natural Light/Organic/Documentary Photography Business

I like a simple, approachable, feminine, earthy/organic feel. Earth/neutral tones, nothing too loud or obnoxious. I like the watercolor look. I don't want anything too trendy or something I'll get tired of after a couple months. As far as colors, I am much more a fan of cream/taupe/blue/green...not a fan of pink or purple at all.

Target Market(s)

Weddings & Families

Industry/Entity Type

Wedding Photography

Contact Information for Business Card

website, email, phone number

Font styles to use
Other font styles liked:
• Horizontes, Gotham

Colors

Designer to choose colors to be used in the design.

Requirements
Must have
• Website: www.mirelhatchway.com
• Phone: 418.629.5073
• Email: mirel@mirelhatchway.com
Nice to have
• I like the watercolor look but its not necessary. I like simple/earthy tones. Nothing too loud or distracting. Simple & feminine without being too girly. I like an approachable/soft feel.
• Instagram: www.instagram.com/mirelhatchwayphotography/
Should not have
• NO loud colors or design or pattern. I do not want a photo of a camera or lens or anything cheesy like that.

```html
<!DOCTYPE html>
<html lang="en">
<head>
<meta charset="UTF-8">
<title>Mirel Hatchway Photography – Business Card</title>
<link href="https://fonts.googleapis.com/css2?family=Montserrat:wght@300;400;500&display=swap" rel="stylesheet">
<style>
  :root {
    --page: #ffffff;
    --card: #797a74;
    --card-edge: #2f302d;
    --ink: #b5b6b2;
    --icon-mark: #ffffff;
  }
  html, body {
    margin: 0;
    padding: 0;
    width: 1200px;
    height: 1200px;
    overflow: hidden;
    background: var(--page);
  }
  .canvas {
    position: relative;
    width: 1200px;
    height: 1200px;
  }
  .card {
    position: absolute;
    left: 27px;
    top: 293px;
    width: 1194px;
    height: 662px;
    background: var(--card);
    border: 1px solid var(--card-edge);
    font-family: "Montserrat", sans-serif;
    color: var(--ink);
  }
  .brand {
    position: absolute;
    left: 84px;
    top: 104px;
    width: 780px;
    text-align: center;
  }
  .brand-name {
    margin: 0;
    font-weight: 300;
    font-size: 70px;
    letter-spacing: 4px;
    line-height: 1;
    white-space: nowrap;
  }
  .brand-tagline {
    margin: 24px 0 0;
    font-weight: 400;
    font-size: 17px;
    letter-spacing: 0.85em;
    line-height: 1;
    padding-left: 0.85em;
  }
  .contact {
    position: absolute;
    right: 284px;
    top: 370px;
    text-align: right;
  }
  .contact-row {
    display: flex;
    align-items: center;
    justify-content: flex-end;
    gap: 30px;
  }
  .contact-text {
    font-weight: 500;
    line-height: 1;
    white-space: nowrap;
  }
  .phone .contact-text { font-size: 51px; }
  .web-mail { margin-top: 28px; align-items: flex-start; }
  .web-mail .lines { display: flex; flex-direction: column; gap: 16px; }
  .web-mail .contact-text { font-size: 42px; }
  .icon {
    width: 44px;
    height: 44px;
    flex: none;
  }
  .icon-disc { fill: var(--ink); }
  .icon-mark { fill: var(--icon-mark); }
  .icon-line { fill: none; stroke: var(--icon-mark); stroke-width: 1.8; stroke-linejoin: round; }
</style>
</head>
<body>
<div class="canvas">
  <section class="card">
    <header class="brand">
      <h1 class="brand-name">Mirel Hatchway</h1>
      <p class="brand-tagline">PHOTOGRAPHY</p>
    </header>

    <div class="contact">
      <div class="contact-row phone">
        <span class="contact-text">418 629 5073</span>
        <svg class="icon" viewBox="0 0 44 44" aria-hidden="true">
          <circle class="icon-disc" cx="22" cy="22" r="22"/>
          <path class="icon-mark" d="M15.2 11.5c.8-.6 1.9-.4 2.4.4l2.3 3.6c.5.8.3 1.8-.4 2.3l-1.4 1c.9 2.3 2.6 4.4 4.8 5.8l1.1-1.3c.6-.7 1.6-.8 2.3-.3l3.5 2.5c.8.6 1 1.7.3 2.5l-1.7 2c-.9 1-2.3 1.4-3.6.9-5.4-2.1-9.5-6.5-11.3-12-.4-1.3 0-2.7 1.1-3.5z"/>
        </svg>
      </div>
      <div class="contact-row web-mail">
        <div class="lines">
          <span class="contact-text">www.mirelhatchway.com</span>
          <span class="contact-text">mirel@mirelhatchway.com</span>
        </div>
        <svg class="icon" viewBox="0 0 44 44" aria-hidden="true">
          <circle class="icon-disc" cx="22" cy="22" r="22"/>
          <rect class="icon-line" x="10.5" y="14.5" width="23" height="15" rx="1.5"/>
          <path class="icon-line" d="M11 15.5l11 8 11-8"/>
        </svg>
      </div>
    </div>
  </section>
</div>
</body>
</html>
```